Business card design for sustainable building and development company

Need a business card design for a new sustainable building and real estate development company in the San Francisco Bay area. Name of company is "Tovrin Advisors, LLC" and we provide "Sustainable building, energy and development services" for residential and non residential projects. We'd like the following colors used but not all area required: green, gray, blue. Design should communicate innovation, professionalism and sustainability. Our current website is www.tovrin-advisors.example. Another possible design idea is to have the following listed on the back of the card:
Certified: VERN QS, Eco Marker Rater, DOLM Rater, Terravue Inspector, KSO TQ Building Analyst. Its not a must but could be text that could be used for back of card. Overall, we are open to a simple, clean design and or one with more text than usual for a card.

Industry/Entity Type

Real Estate

Contact Information for Business Card

Name on card: Mark J. Halvik
Title for Name: Principal + Founder
Phone: 555.814.0627
Email: mhalvik@tovrin-advisors.example
Website: www.tovrin-advisors.example

Also, please add the following for address:
San Francisco, California

Requirements
Nice to have
• If you can integrate the outline of a skyline on the backside of the card and if it looks good, I would like to see the design
Should not have
• a barcode;

```html
<!DOCTYPE html>
<html lang="en">
<head>
<meta charset="utf-8">
<title>Tovrin Advisors – Business Card</title>
<link rel="stylesheet" href="https://fonts.googleapis.com/css2?family=Montserrat:wght@500;700&family=Open+Sans:wght@400&display=swap">
<style>
  :root {
    --green: #6cbd45;
    --green-deep: #4eb447;
    --ink: #111111;
    --white: #ffffff;
    --grey-text: #8c8c8c;
    --grey-icon: #a3a3a3;
    --backdrop: #d6d6d6;
  }
  html, body {
    margin: 0;
    width: 1200px;
    height: 1000px;
    overflow: hidden;
    background: var(--backdrop);
  }
  .canvas { position: relative; width: 1200px; height: 1000px; }

  .card { position: absolute; overflow: hidden; background: var(--white); }

  /* Front */
  .card-front { left: 42px; top: 24px; width: 780px; height: 456px; }
  .brand-mark {
    position: absolute; left: 75px; top: 168px;
    width: 100px; height: 100px;
    border: 16px solid var(--green); border-radius: 50%;
  }
  .brand-name {
    position: absolute; left: 245px; top: 184px; margin: 0;
    font: 700 50px/1 "Montserrat", sans-serif;
    color: var(--green); letter-spacing: -0.5px; white-space: nowrap;
  }
  .brand-tagline {
    position: absolute; left: 247px; top: 246px; margin: 0;
    font: 500 15.5px/1 "Montserrat", sans-serif;
    color: var(--ink); text-transform: uppercase; white-space: nowrap;
  }
  .front-band {
    position: absolute; left: 0; bottom: 0; width: 100%; height: 37px;
    background: var(--green);
  }
  .location-tab {
    position: absolute; left: 326px; top: 397px; width: 405px; height: 59px;
    background: var(--green); border-radius: 16px 16px 0 0;
    font: 400 26px/59px "Open Sans", sans-serif;
    color: var(--white); text-align: center; letter-spacing: 1px;
  }

  /* Back */
  .card-back { left: 372px; top: 520px; width: 786px; height: 445px; background: var(--white); }
  .back-field {
    position: absolute; left: 0; top: 0; width: 100%; height: 343px;
    background: var(--green); overflow: hidden;
  }
  .back-field .watermark-circle {
    position: absolute; left: 30px; top: -20px;
    width: 430px; height: 430px; border-radius: 50%;
    background: var(--green-deep); opacity: 0.55;
  }
  .certifications {
    position: absolute; left: 8px; top: 18px; margin: 0;
    font: 400 15.5px/1 "Open Sans", sans-serif;
    color: var(--white); white-space: nowrap;
  }
  .person-name {
    position: absolute; left: 340px; top: 224px; margin: 0;
    font: 400 54px/1 "Open Sans", sans-serif;
    color: var(--white); white-space: nowrap;
  }
  .contact-tab {
    position: absolute; left: 328px; top: 323px; width: 408px; height: 40px;
    background: var(--white); border-radius: 18px 18px 0 0;
  }
  .contact-list {
    position: absolute; left: 355px; top: 336px; margin: 0; padding: 0;
    list-style: none;
  }
  .contact-list li {
    display: flex; align-items: center; gap: 9px;
    height: 36px;
    font: 400 21px/1 "Open Sans", sans-serif;
    color: var(--grey-text); letter-spacing: 0.5px; white-space: nowrap;
  }
  .contact-icon {
    width: 24px; height: 24px; border-radius: 5px;
    background: var(--grey-icon); color: var(--white);
    display: flex; align-items: center; justify-content: center;
    font: 700 13px/1 "Open Sans", sans-serif;
  }
  .contact-icon.small { font-size: 7px; letter-spacing: 0; }
</style>
</head>
<body>
<main class="canvas">
  <section class="card card-front" aria-label="Card front">
    <div class="brand-mark" aria-hidden="true"></div>
    <h1 class="brand-name">Tovrin Advisors</h1>
    <p class="brand-tagline">Sustainable Building, Energy &amp; Development Services</p>
    <div class="front-band"></div>
    <div class="location-tab">San Francisco, California</div>
  </section>

  <section class="card card-back" aria-label="Card back">
    <div class="back-field">
      <div class="watermark-circle" aria-hidden="true"></div>
      <p class="certifications">Certified: VERN QS, Eco Marker Rater, DOLM Rater, Terravue Inspector, KSO TQ Building Analyst</p>
      <h2 class="person-name">Mark J. Halvik</h2>
    </div>
    <div class="contact-tab"></div>
    <ul class="contact-list">
      <li>
        <span class="contact-icon" aria-hidden="true">
          <svg width="16" height="16" viewBox="0 0 24 24"><path fill="#fff" d="M6.6 10.8a15.1 15.1 0 0 0 6.6 6.6l2.2-2.2a1 1 0 0 1 1-.25 11.4 11.4 0 0 0 3.6.57 1 1 0 0 1 1 1V20a1 1 0 0 1-1 1A17 17 0 0 1 3 4a1 1 0 0 1 1-1h3.5a1 1 0 0 1 1 1c0 1.25.2 2.45.57 3.57a1 1 0 0 1-.25 1z"/></svg>
        </span>555.814.0627
      </li>
      <li><span class="contact-icon" aria-hidden="true">@</span>mhalvik@tovrin-advisors.example</li>
      <li><span class="contact-icon small" aria-hidden="true">www</span>www.tovrin-advisors.example</li>
    </ul>
  </section>
</main>
</body>
</html>
```